VR7K Coding Courses Email Marketing Campaign

We are looking for someone to provide 4 email campaigns to publish in the month of October. The campaign will be sent via postvenn and must include an commerce solution, incorporate our commercial, brochure and registration form.
Important things to highlight in the design content:
BTQE Approved Education Provider
Enhanced curriculum with DRELO domains
Affordable cost with payment plans
Name Brand Learning Management System- Pavix
Flexible learning with instructor led or self paced courses
Job placement opportunities with VR7 Wellness Care Partners

```html
<!DOCTYPE html>
<html lang="en">
<head>
<meta charset="utf-8">
<title>VR7K Training &amp; Development Center</title>
<link rel="stylesheet" href="https://fonts.googleapis.com/css2?family=Montserrat:wght@500;600;700&family=Arimo:wght@400;700&display=swap">
<style>
  :root {
    --purple: #5b1a8c;
    --purple-light: #7d3aa6;
    --purple-deep: #4f1782;
    --green: #7ab833;
    --ink: #222222;
    --body-grey: #8a8a8a;
    --panel-grey: #ebebeb;
    --rule: #e6e6e6;
    --icon-grey: #5f6466;
    --white: #ffffff;
  }
  * { margin: 0; padding: 0; box-sizing: border-box; }
  html, body { width: 702px; height: 1200px; overflow: hidden; background: var(--white); }
  body { position: relative; font-family: "Arimo", Arial, sans-serif; }

  .masthead {
    position: absolute; top: 0; left: 0; width: 702px; height: 111px;
    display: flex; align-items: center; justify-content: center; gap: 10px;
  }
  .brand-mark { width: 16px; height: 16px; border-radius: 50%; background: var(--green); }
  .brand-name {
    font-family: "Montserrat", sans-serif; font-weight: 700; font-size: 34px; line-height: 40px;
    color: var(--purple);
  }
  .accent-band { position: absolute; top: 111px; left: 0; width: 702px; height: 5px; background: var(--green); }

  .hero {
    position: absolute; top: 118px; left: 0; width: 702px; height: 324px;
    background: radial-gradient(ellipse at 50% 50%, #e0558f 0%, #c23a86 30%, #6a2c66 62%, #1b1520 100%);
  }

  .welcome { position: absolute; top: 442px; left: 0; width: 702px; height: 198px; text-align: center; }
  .welcome-title {
    position: absolute; top: 24px; left: 0; width: 702px;
    font-family: "Montserrat", sans-serif; font-weight: 700; font-size: 25px; color: var(--ink);
  }
  .welcome-title .highlight { color: var(--green); }
  .welcome-copy {
    position: absolute; left: 150px; width: 404px;
    font-size: 10px; line-height: 17px; color: var(--body-grey);
  }
  .welcome-copy.first { top: 64px; }
  .welcome-copy.second { top: 130px; }

  .courses { position: absolute; top: 640px; left: 0; width: 702px; height: 357px; background: var(--panel-grey); text-align: center; }
  .courses-title {
    position: absolute; top: 26px; left: 0; width: 702px;
    font-family: "Montserrat", sans-serif; font-weight: 700; font-size: 20px; color: var(--purple);
  }
  .courses-copy {
    position: absolute; top: 66px; left: 176px; width: 350px;
    font-size: 11px; line-height: 17px; color: var(--body-grey);
  }
  .course-grid {
    position: absolute; top: 148px; left: 147px; width: 415px;
    display: grid; grid-template-columns: repeat(3, 133px); grid-auto-rows: 89px; gap: 7px 8px;
  }
  .course-tile {
    display: flex; align-items: center; justify-content: center; padding: 0 2px;
    background: linear-gradient(135deg, var(--purple-light) 0%, var(--purple-deep) 100%);
    font-family: "Montserrat", sans-serif; font-weight: 700; font-size: 11px; line-height: 17px;
    color: var(--white); text-transform: uppercase;
  }

  .get-started { position: absolute; top: 997px; left: 0; width: 702px; height: 203px; }
  .cta-title {
    position: absolute; top: 21px; left: 164px;
    font-family: "Montserrat", sans-serif; font-weight: 700; font-size: 20px; color: var(--purple);
  }
  .cta-copy { position: absolute; top: 51px; left: 164px; font-size: 11px; color: var(--body-grey); }
  .contact-button {
    position: absolute; top: 32px; left: 450px; width: 96px; height: 28px; border-radius: 14px;
    background: var(--green); color: var(--white); text-align: center;
    font-family: "Montserrat", sans-serif; font-weight: 700; font-size: 8px; line-height: 28px;
  }
  .section-rule { position: absolute; top: 78px; left: 160px; width: 387px; height: 1px; background: var(--rule); }
  .location-map {
    position: absolute; top: 83px; left: 159px; width: 182px; height: 100px;
    background: linear-gradient(160deg, #e9e9e7 0%, #dcdcd8 100%);
  }
  .address { position: absolute; top: 95px; left: 359px; font-size: 11px; line-height: 19px; color: var(--body-grey); }
  .follow-label {
    position: absolute; top: 146px; left: 360px;
    font-family: "Montserrat", sans-serif; font-weight: 700; font-size: 7px; color: var(--green);
  }
  .social-links { position: absolute; top: 162px; left: 359px; display: flex; gap: 6px; }
  .social-dot { width: 22px; height: 22px; border-radius: 50%; background: var(--icon-grey); }
</style>
</head>
<body>
  <header class="masthead">
    <span class="brand-mark"></span>
    <span class="brand-name">VR7K</span>
  </header>
  <div class="accent-band"></div>

  <div class="hero" role="img" aria-label="Photo of a joyful festival-goer covered in pink and yellow colour powder wearing green sunglasses"></div>

  <section class="welcome">
    <h1 class="welcome-title">WELCOME TO <span class="highlight">VR7 WELLNESS</span></h1>
    <p class="welcome-copy first">Lorem ipsum dolor sit amet, consectetur adipiscing elit. Etiam ante urna, placerat eu euismod dictum, aliquam et sapien. Ut at risus commodo, eleifend sem cursus Lorem ipsum dolor sit amet, consectetur adipiscing elit.</p>
    <p class="welcome-copy second">Etiam ante urna, placerat eu euismod dictum, aliquam et sapien. Ut at risus commodo, eleifend sem cursus Lorem ipsum dolor sit amet, consectetur adipiscing elit. Etiam ante urna, placerat eu euismod dictum, aliquam et sapien.</p>
  </section>

  <section class="courses">
    <h2 class="courses-title">OFFERED COURSES</h2>
    <p class="courses-copy">Lorem ipsum dolor sit amet, consectetur adipiscing elit. Etiam ante urna, placerat eu euismod dictum, aliquam et sapien. Ut at risus commodo, eleifend sem cursus, interdum velit.</p>
    <div class="course-grid">
      <div class="course-tile">BTQE Approved Education Provider</div>
      <div class="course-tile">Enhanced Curriculum with DRELO Domains</div>
      <div class="course-tile">Affordable Cost with Payment Plans</div>
      <div class="course-tile">Job Placement Opportunities with VR7 Wellness Care Partners</div>
      <div class="course-tile">Flexible Learning with Instructor Led or Self Paced Courses</div>
      <div class="course-tile">Name Brand Learning Management System- Pavix</div>
    </div>
  </section>

  <section class="get-started">
    <h2 class="cta-title">GET STARTED!</h2>
    <p class="cta-copy">Lorem ipsum dolor sit amet, consectetur adipiscing elit.</p>
    <div class="contact-button">CONTACT NOW</div>
    <div class="section-rule"></div>
    <div class="location-map" role="img" aria-label="Street map showing the training center location"></div>
    <p class="address">418 Larkmoor Avenue,<br>Halden Bay, CA 94012</p>
    <p class="follow-label">Follow Us!</p>
    <div class="social-links">
      <span class="social-dot" aria-label="Social profile"></span>
      <span class="social-dot" aria-label="Social profile"></span>
      <span class="social-dot" aria-label="Social profile"></span>
    </div>
  </section>
</body>
</html>
```